Logo and Website Design for QR.KA Horizon - a Software Engineering and IT company

Software engineering and IT are two different disciplines - and yet inseparably linked. At QR.KA Horizon, we combine both worlds and ensure that our software solutions are not only innovative and powerful, but also integrate perfectly into existing IT landscapes. Vision stands more for imagination, so it is not neccessary something what has to do with visualisation. Please consider that the winning competitor is also instructed to make a logo for the company. So please make a suitable logo for QR.KA Horizon to which the website fits to and show it during the website creation process. A good Logo desing is important for winning the competition. The website should contain a landing page with inspiring, perhaps futuristic photos of a datacenter and lines of code. Eventuelly flewent integrated in the text. On the landing page the company should introduced with a small text (max 250 words) followed by a section with a short text to one of our products nearby a graphic visualising the architecture of the product. The menue should be on top and fixed during scrolling and consist of the menue items home, solutions, who are we and a contact button. There should be a footer for linking social media, rights and Impressum. Only as an idea not a must. The very first view on the landing page could also be the menue bar and below of it a transparent unsharp photo (e.g. datacenter, lines of code, both ;) with the company name in the center.

###############################################################

Hi Designers,

Despite your very good approaches for describing QR.KA Horizon, here a short introduction (german text) from ourself:

------
QR.KA Horizon – Ihr Partner für ganzheitliche Softwarelösungen

Die QR.KA Horizon ist ein dynamisches Unternehmen, das sich nicht nur auf die Konzeption, das Design und die Entwicklung maßgeschneiderter Software spezialisiert hat, sondern auch deren reibungslosen Betrieb sicherstellt. Mit einem Team aus erfahrenen Softwarearchitekten und IT-Professionals verbinden wir modernste Softwareentwicklung mit tiefgehendem IT-Know-how – für Lösungen, die nachhaltig, leistungsstark und zukunftssicher sind.

Software Engineering trifft IT – Perfektion in Kombination
Software Engineering und IT sind zwei unterschiedliche Disziplinen – und doch untrennbar miteinander verbunden. Wir bei QR.KA Horizon vereinen beide Welten und sorgen dafür, dass unsere Softwarelösungen nicht nur innovativ und leistungsfähig sind, sondern sich auch perfekt in bestehende IT-Landschaften integrieren.

Expertise mit Fokus auf Healthcare & komplexe IT-Umgebungen
Unsere Experten bringen jahrzehntelange Erfahrung aus dem Healthcare-Sektor mit und unterstützen IT-Abteilungen großer Kliniken in der Entwicklung und Optimierung von Softwarelösungen. Von Anwendungssoftware bis hin zu Steuerungssystemen – unsere Softwareingenieure wissen genau, worauf es ankommt.

Ganzheitlicher Ansatz – über die Software hinaus
Wir entwickeln nicht nur Software, sondern übernehmen auch die Verantwortung für deren stabile und effiziente Betriebsumgebung. Egal, ob on-premises, in der Cloud oder als SaaS-Lösung – wir kümmern uns um den kompletten Lifecycle Ihrer Anwendung.

Ihre Vision – unsere Mission.
Ob Neuentwicklung einer SaaS-Anwendung oder die Migration bestehender Lösungen in eine moderne SaaS-Umgebung – mit QR.KA Horizon haben Sie einen starken Partner an Ihrer Seite.

Lassen Sie uns gemeinsam die Zukunft Ihrer Software gestalten!
--------------

Our first solution called "Clear Record Transfer Gateway" (CLURA)
-------------------
Teilen Sie Ihre Daten sicher – ohne Kompromisse!

Sie nutzen eine relationale Datenbank (Brightcask, Tabulon Hub, Vellumdb etc.) und möchten ausgewählte Daten mit Dritten teilen – sei es für ein Data Warehouse, Business Controller, Lieferanten oder Kunden? Doch dabei sollen Datensicherheit, Integrität und Verfügbarkeit Ihrer primären Lösung in keiner Weise gefährdet werden?

Mit unserer Lösung erhalten Sie genau das: Maximalen Schutz für Ihre Anwendung bei gleichzeitigem Nutzen durch autorisierte Dritte – ganz ohne teure Lizenzkosten für eine Schattendatenbank.

Lassen Sie uns gemeinsam herausfinden, wie Sie Ihre Daten sicher und effizient nutzen können. Kontaktieren Sie uns – wir zeigen Ihnen, was möglich ist!
---------------------

Our second solution MIVO:
---------------------
MIVO – Program for a Tone Matching Instrument ist die smarte Lösung für Unternehmen, die bei Farbgenauigkeit keine Kompromisse machen. Die Software erkennt Farbabweichungen zwischen Mustern vollautomatisch, beschreibt sie verständlich und sorgt so für gleichbleibend hohe Produktqualität – schnell, visuell und präzise. Perfekt für alle, die Farbe zur Vertrauenssache machen.
-------------------------

Thanks,
Gerold

Target Market(s)

IT Professionals from any sector

Industry/Entity Type

Healthcare and other

Coding

Coded - Design and coding required

Number of Pages Required

1 page

Font styles to use
Sans Serif

Colors
0054AA
0677BA
7BADD7
CADEEF
E8F1F8
0094D4
00A9DD
6FCCEA
C7EBF8
E9F6FB
00AB8E
00BBA5
67D7C9
C6EFE9
E9F9F6

Requirements
Must have
• Please see description
Nice to have
• On the landing page the company should introduced with a small text (max 250 words) followed by a section with a short text to one of our products nearby a graphic visualising the architecture of the product. The menue should be on top and fixed during scrolling and consist of the menue items home, solutions, who are we and a contact button. There should be a footer for linking social media, rights and Impressum. Only as an idea not a must. The very first view on the landing page could also be the menue bar and below of it a transparent unsharp photo (e.g. datacenter, lines of code, both ;) with the company name in the center.
Should not have
• Please see description

```html
<!DOCTYPE html>
<html lang="en">
<head>
<meta charset="utf-8">
<title>QR.KA Horizon – Software Engineering &amp; IT</title>
<link rel="stylesheet" href="https://fonts.googleapis.com/css2?family=Jost:wght@400;500;600;700&display=swap">
<style>
:root{
  --blue:#0677BA;
  --blue-bright:#1a8ad0;
  --teal:#00AB8E;
  --teal-soft:#1fb8a0;
  --dark:#0b1120;
  --ink:#1a1a1a;
  --text:#555;
  --partner-bg:#f4f4f4;
  --footer:#333;
  --white:#fff;
}
*{margin:0;padding:0;box-sizing:border-box}
html,body{width:1200px;height:3459px;overflow:hidden}
body{position:relative;font-family:'Jost',sans-serif;color:var(--ink);background:var(--white)}
.abs{position:absolute}
.btn{position:absolute;display:flex;align-items:center;justify-content:center;background:var(--blue);color:var(--white);font-weight:600;font-size:15px;text-transform:uppercase;letter-spacing:.2px}

/* hero */
.hero{position:absolute;left:0;top:0;width:1200px;height:631px;background:linear-gradient(100deg,#05080f 0%,#0c1424 40%,#2a3140 62%,#4a4036 75%,#1a2030 100%)}
.brand{position:absolute;display:flex;align-items:center;gap:12px;color:var(--white);font-weight:600;font-size:22px}
.brand .mark{width:40px;height:40px;border-radius:50%;background:var(--blue-bright)}
.nav{position:absolute;top:27px;left:560px;height:37px;display:flex;align-items:center;font-size:14px;font-weight:500;color:var(--white);text-transform:uppercase}
.nav span{position:absolute;white-space:nowrap}
.nav .active{color:var(--teal-soft)}
.hero-kicker{left:144px;top:297px;color:var(--teal-soft);font-size:15px;font-weight:500}
.hero-title{left:143px;top:330px;color:var(--white);font-size:56px;font-weight:600;letter-spacing:.5px}
.hero-text{left:144px;top:410px;width:450px;color:var(--white);font-size:19px;line-height:32px}
.hero-thumb{left:991px;top:486px;width:209px;height:145px;border:2px solid #cfd6e0;background:linear-gradient(135deg,#5a6a80,#3b4658 60%,#6a7788)}

/* about */
.kicker{color:var(--teal);font-size:16px}
.h2{font-size:37px;font-weight:600;color:var(--ink)}
.rule{height:2px;width:95px;background:var(--teal)}
.lead{font-size:18px;color:var(--ink)}
.body-copy{font-size:13.5px;line-height:24px;color:var(--text);text-align:justify}
.photo{position:absolute}
.vert-word{position:absolute;left:992px;top:848px;width:44px;display:flex;flex-direction:column;align-items:center;color:var(--white);font-size:32px;font-weight:700;line-height:42px}

/* solution */
.solution{left:0;top:1807px;width:600px;height:539px;background:linear-gradient(135deg,#2a8fd6,#1b7fc6 60%,#1672b8)}
.sol-h{left:141px;top:1890px;color:var(--white);font-size:38px;font-weight:600}
.sol-sub{left:145px;top:1950px;width:400px;color:var(--white);font-size:18px;line-height:29px}
.sol-copy{left:146px;top:2015px;width:388px;color:var(--white);font-size:13.5px;line-height:24px;text-align:justify}
.checks{left:144px;top:2128px;color:var(--white);font-size:13px;list-style:none}
.checks li{display:flex;align-items:center;gap:5px;height:31.5px}
.btn-outline{position:absolute;left:145px;top:2246px;width:112px;height:37px;border:2px solid var(--white);color:var(--white);font-size:15px;font-weight:600;display:flex;align-items:center;justify-content:center}

/* products */
.center{left:0;width:1200px;text-align:center}
.prod-num{position:absolute;width:120px;text-align:center;font-size:46px;font-weight:600;color:#e4e4e4}
.prod-icon{position:absolute;width:82px;height:82px;border-radius:50%;background:var(--teal-soft);display:flex;align-items:center;justify-content:center}
.prod-label{position:absolute;width:220px;text-align:center;font-size:16px;color:var(--ink)}

/* partners */
.partners{left:0;top:3020px;width:1200px;height:275px;background:var(--partner-bg)}
.partner{position:absolute;top:3157px;width:218px;height:71px;background:var(--white);display:flex;align-items:center;justify-content:center}
.partner i{display:block;width:130px;height:16px;border-radius:8px;background:#bdbdbd}
.arrow-dot{position:absolute;top:3178px;width:28px;height:28px;border-radius:50%;background:var(--white);box-shadow:0 1px 4px rgba(0,0,0,.2);display:flex;align-items:center;justify-content:center}

/* footer */
.footer{left:0;top:3295px;width:1200px;height:164px;background:var(--footer)}
.foot-nav span{position:absolute;top:3350px;color:var(--white);font-size:14px;text-transform:uppercase}
.copy{top:3422px;color:var(--white);font-size:13px}
</style>
</head>
<body>

<!-- Hero -->
<section class="hero" role="img" aria-label="Photo of two IT engineers with a laptop in a data center aisle"></section>
<div class="brand" style="left:144px;top:27px"><span class="mark"></span>QR.KA Horizon</div>
<nav class="nav">
  <span class="active" style="left:13px">Home</span>
  <span style="left:86px">Who We Are</span>
  <span style="left:206px">Products</span>
  <span style="left:311px">Solution</span>
</nav>
<div class="btn" style="left:964px;top:27px;width:92px;height:37px;font-size:14px">Contact</div>
<div class="abs hero-kicker">Welcome To</div>
<h1 class="abs hero-title">QR.KA HORIZON</h1>
<p class="abs hero-text">Lorem ipsum dolor sit amet, consectetur adipiscing elit, sed do eiusmod tempor incididunt.</p>
<div class="btn" style="left:144px;top:510px;width:142px;height:46px">Get Started</div>
<div class="abs hero-thumb" role="img" aria-label="Photo of engineers gathered around a laptop"></div>
<svg class="abs" style="left:1135px;top:598px" width="50" height="20" viewBox="0 0 50 20" fill="none" stroke="#fff" stroke-width="1.8">
  <path d="M16 10H3M8 5L3 10l5 5"/><path d="M32 10h13M40 5l5 5-5 5"/>
</svg>

<!-- Who we are -->
<div class="abs kicker" style="left:144px;top:696px">About Us</div>
<h2 class="abs h2" style="left:144px;top:727px">WHO WE ARE</h2>
<div class="btn" style="left:942px;top:711px;width:113px;height:41px;font-size:14px">Read More</div>
<div class="abs rule" style="left:143px;top:863px"></div>
<div class="abs lead" style="left:143px;top:879px">Lorem ipsum dolor sit amet, consectetur</div>
<div class="abs body-copy" style="left:143px;top:918px;width:429px">
  <p>Sed ut perspiciatis unde omnis iste natus error sit voluptatem accusantium doloremque laudantium, totam rem aperiam, eaque ipsa quae ab illo inventore veritatis et quasi architecto beatae vitae dicta sunt explicab tempor incididunt ut labore et dolore</p>
  <p style="margin-top:6px">Duis aute irure dolor in reprehenderit in voluptate velit esse cillum dolore eu fugiat nulla pariatur. Excepteur sint occaecat cupidatat non proident, sunt in culpa qui officia deserunt mollit anim id est laborum.Nemo enim ipsam voluptatem quia voluptas sit aspernatur aut odit aut fugit, sed quia consequuntur magni dolores eos qui ratione voluptatem sequi nesciunt.</p>
</div>
<div class="photo" style="left:632px;top:832px;width:423px;height:367px;background:linear-gradient(120deg,#e6eef0 0%,#9fc9c6 45%,#1fa891 100%)" role="img" aria-label="Photo of a developer with a laptop in front of code screens"></div>
<div class="vert-word"><span>W</span><span>H</span><span>O</span><span>W</span><span>E</span><span>A</span><span>R</span><span>E</span></div>

<!-- Mission -->
<div class="photo" style="left:142px;top:1278px;width:455px;height:435px;background:linear-gradient(120deg,#dfe4e6 0%,#c9cfd2 50%,#d9a283 80%,#e3e6e8 100%)" role="img" aria-label="Photo of a smiling IT professional holding a tablet in an office"></div>
<h2 class="abs h2" style="left:693px;top:1300px">MISSION &amp; VISION</h2>
<div class="photo" style="left:691px;top:1368px;width:364px;height:216px;background:linear-gradient(120deg,#58646f,#2e363e 55%,#6f7a84)" role="img" aria-label="Photo of an engineering team working at computers"></div>
<div class="abs lead" style="left:690px;top:1610px">Lorem Ipsum Dolor</div>
<p class="abs body-copy" style="left:691px;top:1641px;width:366px;text-align:left">quis nostrum exercitationem ullam corporis suscipit laboriosam, nisi ut aliquid ex ea commodi Quis autem vel eum iure reprehenderit</p>

<!-- Solution -->
<section class="abs solution"></section>
<div class="abs rule" style="left:143px;top:1879px;background:#fff"></div>
<h2 class="abs sol-h">SOLUTION</h2>
<p class="abs sol-sub">Sed ut perspiciatis unde omnis iste natus error sit voluptatem accusantium dolore</p>
<p class="abs sol-copy">Duis aute irure dolor in reprehenderit in voluptate velit esse cillum dolore eu fugiat nulla pariatur. Excepteur sint occaecat cupidatat non proident, sunt in culpa qui officia deserunt mollit anim id est laborum,nemo enim ipsam</p>
<ul class="abs checks">
  <li><svg width="12" height="12" viewBox="0 0 12 12"><circle cx="6" cy="6" r="6" fill="#fff"/><path d="M3.2 6.2l2 2 3.6-4" stroke="#1b7fc6" stroke-width="1.6" fill="none"/></svg>Ut enim ad minim veniam, quis nostrud</li>
  <li><svg width="12" height="12" viewBox="0 0 12 12"><circle cx="6" cy="6" r="6" fill="#fff"/><path d="M3.2 6.2l2 2 3.6-4" stroke="#1b7fc6" stroke-width="1.6" fill="none"/></svg>Duis aute irure dolor in reprehenderit</li>
  <li><svg width="12" height="12" viewBox="0 0 12 12"><circle cx="6" cy="6" r="6" fill="#fff"/><path d="M3.2 6.2l2 2 3.6-4" stroke="#1b7fc6" stroke-width="1.6" fill="none"/></svg>Sed ut perspiciatis unde omnis iste natus error</li>
</ul>
<div class="btn-outline">CONTACT</div>
<div class="photo" style="left:600px;top:1807px;width:600px;height:539px;background:linear-gradient(110deg,#2b3440 0%,#3d5a8a 45%,#1c2430 75%,#0f1a22 100%)" role="img" aria-label="Photo of an engineer typing on a laptop beside server racks"></div>

<!-- Products -->
<h2 class="abs center h2" style="top:2422px;font-size:36px">PRODUCTS</h2>
<p class="abs" style="left:195px;top:2488px;width:810px;text-align:center;font-size:18px;line-height:29px;color:var(--text)">Lorem ipsum dolor sit amet, consectetur adipiscing elit, sed do eiusmod tempor incididunt ut labore et dolore magna aliqua. Ut enim ad minim veniam,</p>
<div class="photo" style="left:428px;top:2607px;width:344px;height:263px;background:linear-gradient(120deg,#1f3550,#2f4f6e 50%,#5a6f7e)" role="img" aria-label="Photo of two colleagues reviewing a tablet with data overlays"></div>

<div class="prod-num" style="left:192px;top:2545px">01</div>
<div class="prod-icon" style="left:211px;top:2587px"><svg width="44" height="44" viewBox="0 0 44 44" fill="none" stroke="#fff" stroke-width="1.8"><rect x="6" y="8" width="32" height="26" rx="3"/><path d="M12 22l6 5 6-5 6 5M14 18h16"/></svg></div>
<div class="prod-label" style="left:142px;top:2694px">Business Connections</div>

<div class="prod-num" style="left:192px;top:2730px">02</div>
<div class="prod-icon" style="left:211px;top:2772px"><svg width="44" height="44" viewBox="0 0 44 44" fill="none" stroke="#fff" stroke-width="1.8"><circle cx="14" cy="14" r="4"/><circle cx="30" cy="14" r="4"/><path d="M8 34v-8a6 6 0 0112 0v8M24 34v-8a6 6 0 0112 0v8"/></svg></div>
<div class="prod-label" style="left:142px;top:2878px">Marketing Consultation</div>

<div class="prod-num" style="left:912px;top:2545px">03</div>
<div class="prod-icon" style="left:931px;top:2587px"><svg width="44" height="44" viewBox="0 0 44 44" fill="none" stroke="#fff" stroke-width="1.8"><circle cx="12" cy="13" r="3.5"/><circle cx="22" cy="11" r="3.5"/><circle cx="32" cy="13" r="3.5"/><path d="M6 32v-6a6 6 0 0112 0M16 32v-8a6 6 0 0112 0v8M26 26a6 6 0 0112 0v6"/></svg></div>
<div class="prod-label" style="left:862px;top:2694px">Government Relations</div>

<div class="prod-num" style="left:912px;top:2730px">04</div>
<div class="prod-icon" style="left:931px;top:2772px"><svg width="44" height="44" viewBox="0 0 44 44" fill="none" stroke="#fff" stroke-width="1.8"><rect x="6" y="8" width="32" height="22" rx="2"/><path d="M12 26v-6M18 26v-10M24 26v-8M30 26v-12M16 36h12"/></svg></div>
<div class="prod-label" style="left:862px;top:2878px">Market Research</div>

<svg class="abs" style="left:320px;top:2650px" width="560" height="150" viewBox="0 0 560 150" fill="none" stroke="#aab4bc" stroke-width="1.6" stroke-dasharray="4 4">
  <path d="M102 40L16 12M10 10l10 0M10 10l6 8"/>
  <path d="M102 110L10 130M4 132l9-5M4 132l9 4"/>
  <path d="M458 40L548 12M554 10l-10 0M554 10l-6 8"/>
  <path d="M458 110L552 128M558 130l-9-5M558 130l-8 5"/>
</svg>
<div class="btn" style="left:536px;top:2907px;width:127px;height:38px;font-size:14px">Learn More</div>

<!-- Partners -->
<section class="abs partners"></section>
<h2 class="abs center h2" style="top:3082px;font-size:33px">OUR PARTNERS</h2>
<div class="arrow-dot" style="left:80px"><svg width="10" height="10" viewBox="0 0 10 10"><path d="M7 1L2 5l5 4z" fill="#333"/></svg></div>
<div class="partner" style="left:144px"><i></i></div>
<div class="partner" style="left:376px"><i></i></div>
<div class="partner" style="left:607px"><i></i></div>
<div class="partner" style="left:838px"><i></i></div>
<div class="arrow-dot" style="left:1091px"><svg width="10" height="10" viewBox="0 0 10 10"><path d="M3 1l5 4-5 4z" fill="#333"/></svg></div>

<!-- Footer -->
<footer class="abs footer"></footer>
<div class="brand" style="left:144px;top:3336px"><span class="mark"></span>QR.KA Horizon</div>
<div class="foot-nav">
  <span style="left:581px">Home</span>
  <span style="left:657px">Who We Are</span>
  <span style="left:779px">Products</span>
  <span style="left:885px">Solutions</span>
  <span style="left:994px">Contact</span>
</div>
<div class="abs center copy">Copyrights@2025 QR.KA Horizon &nbsp;- Privacy Policy -Term &amp; Conditions</div>

</body>
</html>
```